Support Welcome Packet Redesign

Looking to redesign our current "welcome packet" that we send to our new customers to help them understand our support service. It is currently in Microsoft Word and would like to remain in either word or publisher. Something that we can easily edit, as the content adjusts based on the customer needs. We want this document to be simple and understandable as it should be something our customers can reference at any time during our contract and easy to navigate.

Target Market(s)

Current Customers. Healthcare, Oil & Gas, Transportation, etc.

Industry/Entity Type

It Service

Font styles to use
Sans Serif

Requirements
Must have
• Table of Contents, inVex Logo and current content
Nice to have
• Easy navigation. Redone final page (contact info)

```html
<!DOCTYPE html>
<html lang="en">
<head>
<meta charset="utf-8">
<title>inVex Support Information</title>
<link href="https://fonts.googleapis.com/css2?family=Carlito:wght@400;700&display=swap" rel="stylesheet">
<style>
  :root {
    --orange: #f7821e;
    --orange-deep: #ef6f0c;
    --ink: #1e1e1e;
    --muted: #444;
    --bg-top: #ececec;
    --bg-bottom: #ffffff;
    --blue: #3f8fd6;
    --yellow: #f7d21c;
    --green: #6bb43c;
  }
  * { margin: 0; padding: 0; box-sizing: border-box; }
  html, body { width: 848px; height: 1200px; overflow: hidden; }
  body { font-family: "Carlito", "Calibri", sans-serif; color: var(--ink); }
  .page {
    position: relative; width: 848px; height: 1200px; overflow: hidden;
    background: linear-gradient(180deg, var(--bg-top) 0%, var(--bg-bottom) 55%, #f4f4f4 100%);
  }
  .header-art { position: absolute; left: 0; top: 0; }
  .page-title {
    position: absolute; left: 80px; top: 54px;
    font-size: 32px; font-weight: 700; color: #fff;
    text-shadow: 1px 2px 3px rgba(0,0,0,.25);
  }
  .brand-panel {
    position: absolute; left: 690px; top: 0; width: 116px; height: 192px;
    background: #fff; display: flex; flex-direction: column; align-items: center; justify-content: center; gap: 10px;
  }
  .brand-mark { width: 34px; height: 34px; background: var(--orange); }
  .brand-name { font-size: 26px; font-weight: 700; color: #555; }
  .section-label { position: absolute; left: 80px; top: 333px; font-size: 16px; font-weight: 700; }
  .intro {
    position: absolute; left: 80px; top: 368px; width: 700px;
    font-size: 21px; line-height: 27.5px;
  }
  .intro .callout { color: var(--orange); font-weight: 700; }
  .priority-heading { position: absolute; left: 80px; top: 548px; font-size: 21px; }
  .priority {
    position: absolute; left: 80px; width: 700px;
    display: grid; grid-template-columns: 149px 1fr;
    font-size: 17.5px; line-height: 25.5px;
  }
  .priority dt { font-weight: 700; }
  .p1 { top: 587px; } .p2 { top: 688px; } .p3 { top: 812px; } .p4 { top: 912px; }
  .footer {
    position: absolute; left: 54px; top: 1066px; width: 740px;
    display: flex; align-items: center; font-size: 15px; color: #333;
  }
  .footer-brand { display: flex; align-items: center; gap: 6px; font-size: 20px; font-weight: 700; color: #555; margin-right: 18px; }
  .footer-brand .sq { width: 18px; height: 18px; background: var(--orange); }
  .footer-item { display: flex; align-items: center; gap: 5px; margin-right: 20px; }
  .footer-rule {
    position: absolute; left: 8px; top: 1098px; width: 840px; height: 8px;
    background: linear-gradient(90deg, var(--blue) 0 26%, var(--orange) 26% 50%, var(--yellow) 50% 75%, var(--green) 75% 100%);
    opacity: .9;
  }
  .page-number { position: absolute; left: 774px; top: 1118px; font-size: 20px; }
</style>
</head>
<body>
<div class="page">
  <svg class="header-art" width="848" height="270" viewBox="0 0 848 270">
    <polygon points="0,0 495,0 670,250 0,115" fill="var(--orange)"/>
    <polygon points="0,0 300,0 0,90" fill="var(--orange-deep)" opacity=".5"/>
    <g role="img" aria-label="Decorative gear graphic">
      <circle cx="330" cy="140" r="72" fill="var(--orange-deep)"/>
      <circle cx="250" cy="95" r="38" fill="var(--orange-deep)"/>
    </g>
    <path d="M495,0 L710,215 Q735,245 790,245 L848,245" fill="none" stroke="var(--orange)" stroke-width="4"/>
  </svg>
  <h1 class="page-title">Support Information</h1>
  <div class="brand-panel">
    <span class="brand-mark"></span>
    <span class="brand-name">inVex</span>
  </div>

  <h2 class="section-label">inVex Support Escalation Matrix</h2>
  <p class="intro">This Support Escalation Matrix describes the conditions and path for the escalation of technical support issues.&nbsp; The Support Escalation Matrix also provides the process and contact information for the Management Team responsible for your account.&nbsp; <span class="callout">Please see the section ‘About the Support Teams’ for a description of the role of inVex teams.</span></p>

  <h3 class="priority-heading">Priority Level</h3>
  <dl class="priority p1"><dt>Priority Level 1:</dt><dd>The issue has caused a critical impact to your business operations or there is a service outage.&nbsp; Support will be provided outside of normal business hours as required.</dd></dl>
  <dl class="priority p2"><dt>Priority Level 2:</dt><dd>The performance of an existing service has been impacted/downgraded or significant aspects of your business operation are negatively affected by inadequate performance of inVex products.&nbsp; Support will be provided during normal business hours.</dd></dl>
  <dl class="priority p3"><dt>Priority Level 3:</dt><dd>Operational performance of your inVex service is impaired, but most business operations remain functional. Support will be provided during normal business hours.</dd></dl>
  <dl class="priority p4"><dt>Priority Level 4:</dt><dd>You require information or assistance with inVex product/service capabilities, installation or basic configuration. There is little or no effect on your business operations.</dd></dl>

  <footer class="footer">
    <span class="footer-brand"><span class="sq"></span>inVex Technology</span>
    <span class="footer-item">
      <svg width="14" height="18" viewBox="0 0 14 18"><path d="M7 0C3 0 0 3 0 7c0 5 7 11 7 11s7-6 7-11c0-4-3-7-7-7z" fill="var(--blue)"/><circle cx="7" cy="7" r="2.5" fill="#fff"/></svg>
      482 W Alder Ave&nbsp; Tempe, AZ 85281</span>
    <span class="footer-item">
      <svg width="16" height="16" viewBox="0 0 24 24"><path d="M6.6 10.8a15 15 0 006.6 6.6l2.2-2.2c.3-.3.7-.4 1-.2 1.1.4 2.3.6 3.6.6.6 0 1 .4 1 1V20c0 .6-.4 1-1 1A17 17 0 013 4c0-.6.4-1 1-1h3.5c.6 0 1 .4 1 1 0 1.3.2 2.5.6 3.6.1.3 0 .7-.2 1z" fill="var(--blue)"/></svg>
      480-555-0192</span>
    <span class="footer-item">
      <svg width="16" height="16" viewBox="0 0 16 16"><circle cx="8" cy="8" r="7.5" fill="var(--blue)"/><path d="M1 8h14M8 1c3 3 3 11 0 14M8 1c-3 3-3 11 0 14" stroke="#fff" fill="none"/></svg>
      www.INVEXCORP.com</span>
  </footer>
  <div class="footer-rule"></div>
  <div class="page-number">6</div>
</div>
</body>
</html>
```